RB Halden Electric Yard Sign

Looking to have a yard sign designed that we can place at projects we are working on. Most likely will be 18" H x 24" W but flexible that we can increase the size if necessary. It should include our logo, our phone # 609-555-0147, website rbhaldenelectric.example and slogan, built on integrity, driven by excellence. Colors should match our brand.

```html
<!DOCTYPE html>
<html lang="en">
<head>
<meta charset="utf-8">
<title>RB Halden Electric – Yard Sign &amp; Business Card</title>
<link rel="stylesheet" href="https://fonts.googleapis.com/css2?family=Montserrat:wght@400;500;600;700;800&display=swap">
<style>
  :root {
    --backdrop: #a4a4a4;
    --white: #ffffff;
    --navy: #1b3766;
    --red: #d9202a;
    --card-face: #eeeae4;
    --ink: #2b2b2b;
  }
  * { box-sizing: border-box; margin: 0; padding: 0; }
  html, body { width: 1059px; height: 1200px; overflow: hidden; }
  body {
    position: relative;
    background: var(--backdrop);
    font-family: "Montserrat", sans-serif;
  }

  /* Yard sign */
  .yard-sign {
    position: absolute;
    left: 204px; top: 77px;
    width: 652px; height: 489px;
    background: var(--white);
    box-shadow: 4px 6px 10px rgba(0,0,0,.45);
  }
  .sign-brand {
    position: absolute; left: 0; right: 0; top: 62px;
    text-align: center;
  }
  .brand-name {
    color: var(--red);
    font-weight: 800;
    font-size: 50px;
    letter-spacing: 2px;
    line-height: 1;
  }
  .brand-role {
    margin-top: 14px;
    color: var(--navy);
    font-weight: 700;
    font-size: 26px;
    letter-spacing: 7px;
    line-height: 1;
  }
  .brand-rule {
    display: block;
    margin: 8px auto 0;
    width: 552px; height: 4px;
    background: var(--red);
  }
  .contact-band {
    position: absolute; left: 0; right: 0; top: 257px;
    height: 124px;
    background: var(--navy);
    color: var(--white);
    text-align: center;
  }
  .contact-phone {
    font-weight: 600;
    font-size: 64px;
    line-height: 1;
    margin-top: 10px;
    letter-spacing: 1px;
  }
  .contact-web {
    font-weight: 500;
    font-size: 32px;
    line-height: 1;
    margin-top: 8px;
  }
  .slogan {
    position: absolute; left: 0; right: 0; top: 423px;
    text-align: center;
    color: var(--navy);
    font-weight: 500;
    font-size: 29px;
    line-height: 1;
  }

  /* Business card */
  .business-card {
    position: absolute;
    left: 319px; top: 773px;
    width: 443px; height: 240px;
    background: var(--card-face);
    border-radius: 10px;
    box-shadow: 2px 4px 10px rgba(0,0,0,.3);
  }
  .card-brand {
    position: absolute; left: 20px; top: 100px;
    width: 210px;
    text-align: center;
  }
  .card-brand .brand-name { font-size: 19px; letter-spacing: 1px; }
  .card-brand .brand-role { font-size: 10px; letter-spacing: 2.6px; margin-top: 5px; }
  .card-brand .brand-rule { width: 192px; height: 2px; margin-top: 3px; }
  .card-divider {
    position: absolute; left: 231px; top: 55px;
    width: 2px; height: 131px;
    background: var(--red);
  }
  .card-details {
    position: absolute; left: 243px; top: 56px;
    color: var(--ink);
    font-size: 10.5px;
    line-height: 1.6;
  }
  .card-name {
    color: var(--red);
    font-weight: 700;
    font-size: 18px;
    line-height: 1.1;
  }
  .card-title { font-size: 11.5px; margin-bottom: 8px; }
  .card-address { margin-bottom: 8px; }
  .card-line { display: flex; align-items: center; gap: 5px; }
  .card-line svg { width: 9px; height: 9px; flex: none; }
</style>
</head>
<body>

<section class="yard-sign" aria-label="Yard sign">
  <div class="sign-brand">
    <div class="brand-name">R.B. HALDEN</div>
    <div class="brand-role">Electrical Contractor</div>
    <span class="brand-rule"></span>
  </div>
  <div class="contact-band">
    <div class="contact-phone">609-555-0147</div>
    <div class="contact-web">rbhaldenelectric.example</div>
  </div>
  <p class="slogan">Built on integrity, driven by excellence</p>
</section>

<section class="business-card" aria-label="Business card">
  <div class="card-brand">
    <div class="brand-name">R.B. HALDEN</div>
    <div class="brand-role">Electrical Contractor</div>
    <span class="brand-rule"></span>
  </div>
  <div class="card-divider"></div>
  <div class="card-details">
    <div class="card-name">R.B. Halden</div>
    <div class="card-title">Electrical Contractor</div>
    <div class="card-address">2400 N. Cedar Bridge Rd.<br>Millbrook, NJ 08099</div>
    <div class="card-line">
      <svg viewBox="0 0 10 10" aria-hidden="true"><path fill="#d9202a" d="M2 1 L4 1 L4.6 3.2 L3.4 4 Q4.2 5.8 6 6.6 L6.8 5.4 L9 6 L9 8 Q8.6 9 7.6 9 Q1 8.4 1 2.4 Q1 1.2 2 1Z"/></svg>
      609-555-0147
    </div>
    <div class="card-line">
      <svg viewBox="0 0 10 10" aria-hidden="true"><rect x="0.5" y="2" width="9" height="6" fill="#d9202a"/><path d="M0.5 2 L5 5.5 L9.5 2" stroke="#fff" stroke-width="0.9" fill="none"/></svg>
      service@rbhaldenelectric.example
    </div>
    <div class="card-line">
      <svg viewBox="0 0 10 10" aria-hidden="true"><circle cx="5" cy="5" r="4.3" fill="#d9202a"/><path d="M0.7 5 H9.3 M5 0.7 Q2.5 5 5 9.3 M5 0.7 Q7.5 5 5 9.3" stroke="#fff" stroke-width="0.7" fill="none"/></svg>
      rbhaldenelectric.example
    </div>
  </div>
</section>

</body>
</html>
```